Company website for an international IT business

We require a website for our business, Korvel Solutions. The business has two primary areas: Lanterns, which includes two machine learning/deep learning based products and IT consultancy, which is the service we provide to other businesses.

We bridge cutting-edge research to market.

STYLING:
The site can be on single page or multi-page. This is fully open to suggestion. So long as the look and feel are consistent. Currently, we have no strong preference for colors, styles or layouts.
You can find the logo of our website in the attachment “Korvel-logo.png” and “Korvel-logo-landscape.png”.

CONTENT:
You can find the text of the website in “Website-Content.pdf”, which explains the services and products of our business. The format of the text is also open to suggestion - including breaking up the text into visually appealing sections.
We would also like to include suitable images on the website so that it does not appear to be a text-heavy page. We are happy to have placeholder images on stock image sites if needed. We are open to suggestions on placing of images

ATTACHMENT:

Industry/Entity Type

It Company

Coding

Coded - Design and coding required

Number of Pages Required

1 page

Colors

Designer to choose colors to be used in the design.

Requirements
Must have
• A full description of the requirement is in the attachment "Website-Content.pdf"
• The design must have HTML/CSS, and all resources relevant (images, fonts etc)
• We are
Nice to have
• We are open to suggestions on top of the requirement, please reach out and communicate.

```html
<!DOCTYPE html>
<html lang="en">
<head>
<meta charset="utf-8">
<title>Korvel Solutions</title>
<link rel="stylesheet" href="https://fonts.googleapis.com/css2?family=Exo+2:wght@500;600;700&family=Open+Sans:ital,wght@0,400;0,600;0,700;1,400&display=swap">
<style>
:root{
  --blue:#0a80c4;
  --blue-dark:#066aa6;
  --ink:#1b1b1b;
  --text:#4a4a4a;
  --band:#ededed;
  --white:#ffffff;
  --footer:#1c1c1c;
}
*{box-sizing:border-box;margin:0;padding:0}
html,body{width:1200px;height:3377px;overflow:hidden}
body{position:relative;background:var(--white);font-family:"Open Sans",Arial,sans-serif;color:var(--text)}
.abs{position:absolute}
.heading{font-family:"Exo 2",Arial,sans-serif;font-weight:600;color:var(--ink);letter-spacing:.5px}
.btn{position:absolute;display:flex;align-items:center;justify-content:center;background:var(--blue);color:var(--white);font-family:"Exo 2",Arial,sans-serif;font-weight:600;font-size:21px;border-radius:6px;box-shadow:0 4px 6px rgba(0,0,0,.25)}

/* header */
.site-header{position:absolute;left:0;top:0;width:1200px;height:95px;background:var(--white);border-top:4px solid var(--blue);box-shadow:0 2px 6px rgba(0,0,0,.15);z-index:3}
.brand{position:absolute;left:78px;top:12px;display:flex;align-items:center;gap:14px}
.brand-dot{width:66px;height:66px;border-radius:50%;background:var(--blue)}
.brand-name{font-family:"Exo 2",Arial,sans-serif;font-weight:700;font-size:24px;color:var(--ink)}
.nav{position:absolute;top:0;left:0;font-family:"Exo 2",Arial,sans-serif;font-size:15px;font-weight:500;color:var(--ink)}
.nav span{position:absolute;top:37px;white-space:nowrap}
.nav .active{top:-4px;left:509px;width:81px;height:128px;background:var(--blue);color:var(--white);border-radius:0 0 26px 26px;display:flex;justify-content:center;padding-top:41px}

/* hero */
.hero{position:absolute;left:0;top:95px;width:1200px;height:581px;background:linear-gradient(180deg,#3b3a36 0%,#2a2926 45%,#1b1a19 100%);overflow:hidden}
.hero-shade{position:absolute;inset:0;background:radial-gradient(ellipse at 45% 40%,rgba(120,110,90,.45),rgba(0,0,0,0) 60%)}
.hero h1{position:absolute;top:162px;width:100%;text-align:center;font-family:"Open Sans",Arial,sans-serif;font-weight:700;font-size:88px;color:var(--white);letter-spacing:-1px}
.hero p{position:absolute;top:274px;width:100%;text-align:center;font-weight:700;font-size:30px;color:var(--white)}
.hero .btn{left:509px;top:344px;width:184px;height:54px;box-shadow:none;font-size:22px}

/* welcome */
.welcome h2{position:absolute;top:733px;width:100%;text-align:center;font-size:40px}
.welcome .lead{position:absolute;top:790px;left:170px;width:860px;text-align:center;font-size:14px;line-height:27px}
.step-icon{position:absolute;top:892px;width:102px;height:102px;border-radius:50%;background:var(--blue)}
.step-icon svg{position:absolute;left:26px;top:26px}
.step-title{position:absolute;top:886px;font-family:"Exo 2",Arial,sans-serif;font-weight:700;font-size:24px;color:var(--blue)}
.step-text{position:absolute;top:925px;width:212px;font-size:13px;line-height:25px}

/* product bands */
.band{position:absolute;left:0;width:1200px;background:var(--band);overflow:hidden}
.product-title{position:absolute;font-size:42px}
.product-copy{position:absolute;font-size:14px;line-height:27px}
.product-copy p{margin-bottom:11px}
.frame{position:absolute;border:3px solid var(--white);box-shadow:0 2px 8px rgba(0,0,0,.2)}
.dots{position:absolute;display:flex;gap:9px}
.dots i{width:15px;height:15px;border-radius:50%;border:2px solid var(--white);display:block}
.dots i.on{background:var(--white)}

/* expertise */
.expertise h2{position:absolute;top:1662px;width:100%;text-align:center;font-size:40px}
.expertise .quote{position:absolute;top:1724px;left:220px;width:760px;text-align:center;font-style:italic;font-size:17px;line-height:30px}
.expertise h3{position:absolute;top:1800px;width:100%;text-align:center;font-family:"Exo 2",Arial,sans-serif;font-weight:700;font-size:29px;color:var(--blue)}
.skill{position:absolute;top:1884px;width:240px;text-align:center;font-size:15.5px;color:var(--ink)}
.skill svg{display:block;margin:0 auto 14px}

/* help */
.help h2{position:absolute;top:2614px;width:100%;text-align:center;font-size:40px}
.help-item{position:absolute;top:2710px;display:flex;align-items:center}
.help-item .rule{width:4px;height:72px;background:#d6d6d6;margin:0 22px}
.help-item p{width:210px;font-size:13.5px;line-height:26px}

/* contact */
.contact{position:absolute;left:0;top:2844px;width:1200px;height:466px;background:linear-gradient(135deg,#1b8fd2 0%,#0a7cc0 55%,#0868a8 100%);color:var(--white)}
.contact h2{position:absolute;top:58px;width:100%;text-align:center;font-family:"Exo 2",Arial,sans-serif;font-weight:600;font-size:40px;color:var(--white)}
.contact .sub{position:absolute;top:114px;width:100%;text-align:center;font-size:17px}
.field{position:absolute;background:rgba(255,255,255,.2);border:1px solid rgba(255,255,255,.55);border-radius:3px;font-size:13px;color:rgba(255,255,255,.85);padding:8px 14px}
.contact .btn{left:77px;top:353px;width:693px;height:54px}
.info{position:absolute;left:814px;font-size:13px;line-height:21px}
.info svg{position:absolute;left:0;top:0}
.info div{position:absolute;left:46px;white-space:nowrap}
.social{position:absolute;top:362px;width:44px;height:44px;border-radius:50%;border:2px solid var(--white)}

.site-footer{position:absolute;left:0;top:3310px;width:1200px;height:67px;background:var(--footer);color:#cfcfcf;font-size:14px;display:flex;align-items:center;justify-content:center}
</style>
</head>
<body>

<header class="site-header">
  <div class="brand"><span class="brand-dot"></span><span class="brand-name">KORVEL</span></div>
  <nav class="nav">
    <span class="active">HOME</span>
    <span style="left:610px">ABOUT US</span>
    <span style="left:712px">LANTERNS</span>
    <span style="left:815px">IT CONSULTANCY</span>
    <span style="left:982px">CONTACT US</span>
    <svg class="abs" style="left:1102px;top:36px" width="22" height="22" viewBox="0 0 22 22"><circle cx="9" cy="9" r="6.5" fill="none" stroke="#0a80c4" stroke-width="3"/><line x1="14" y1="14" x2="20" y2="20" stroke="#0a80c4" stroke-width="3.5" stroke-linecap="round"/></svg>
  </nav>
</header>

<section class="hero" role="img" aria-label="Photo of two colleagues in a meeting at a table by a large window">
  <div class="hero-shade"></div>
  <h1>Korvel Solutions</h1>
  <p>We Solve “HARD” Problems For Business</p>
  <span class="btn">CONTACT US</span>
  <svg class="abs" style="left:26px;top:270px" width="20" height="46" viewBox="0 0 20 46"><polyline points="18,2 3,23 18,44" fill="none" stroke="#fff" stroke-width="2"/></svg>
  <svg class="abs" style="left:1154px;top:270px" width="20" height="46" viewBox="0 0 20 46"><polyline points="2,2 17,23 2,44" fill="none" stroke="#fff" stroke-width="2"/></svg>
</section>

<section class="welcome">
  <h2 class="heading">WELCOME TO KORVEL</h2>
  <p class="lead">Korvel Solutions is an IT consultancy firm with a difference We can provide IT expertise for your business at any stage -<br>from initial idea to live systems.</p>

  <div class="step-icon" style="left:79px"><svg width="50" height="50" viewBox="0 0 50 50" fill="none" stroke="#fff" stroke-width="2.5"><rect x="10" y="5" width="30" height="40" rx="3"/><line x1="16" y1="15" x2="34" y2="15"/><line x1="16" y1="22" x2="34" y2="22"/><line x1="16" y1="29" x2="34" y2="29"/><line x1="16" y1="36" x2="28" y2="36"/></svg></div>
  <div class="step-title" style="left:203px">DEFINE</div>
  <p class="step-text" style="left:203px">Our conversation will start with a high-level agreement on the overall strategy Our tech team will research &amp; investigate.</p>

  <div class="step-icon" style="left:432px"><svg width="50" height="50" viewBox="0 0 50 50" fill="none" stroke="#fff" stroke-width="2.5"><path d="M8 12h12a5 5 0 1 1 10 0h12v12a5 5 0 1 0 0 10v10H8V34a5 5 0 1 0 0-10z"/></svg></div>
  <div class="step-title" style="left:558px">BUILD</div>
  <p class="step-text" style="left:558px">We follow a scrum methodolog -gy in our development proces that is, we carry out the work in multiple (bi-)weekly sprints.</p>

  <div class="step-icon" style="left:788px"><svg width="52" height="50" viewBox="0 0 52 50" fill="none" stroke="#fff" stroke-width="2.5"><rect x="3" y="12" width="30" height="22"/><path d="M33 18h9l7 8v8H33z"/><circle cx="13" cy="38" r="4"/><circle cx="41" cy="38" r="4"/></svg></div>
  <div class="step-title" style="left:914px">DELIVER</div>
  <p class="step-text" style="left:914px">At the end of a contract, we ship deliverables with sufficient documentations. In addition, we will provide free support</p>
</section>

<section class="band" style="top:1088px;height:520px">
  <svg class="abs" style="left:0;top:0" width="1200" height="520" viewBox="0 0 1200 520"><polygon points="1110,0 1200,0 1200,120" fill="#0a80c4"/><polygon points="680,520 760,455 1200,455 1200,520" fill="#0a80c4"/></svg>
  <h2 class="heading product-title" style="left:77px;top:70px">VIGIL</h2>
  <div class="product-copy" style="left:77px;top:128px;width:555px">
    <p>The primary cause of accidents on the road are caused by human error. Of these driver distraction and fatigue are the real problem.</p>
    <p>VIGIL is a system for HGV/HMT drivers to make every journey safer - safer for the driver and safer to other road users.</p>
    <p>VIGIL uses advanced deep learning techniques to monitor driver behavior in real time inside the cabin. VIGIL can detect driver distraction (mobile phone usage, smoking, failure to focused on the road ahead) and also monitor for classic signs of fatigue. Current ADAS systems focus on external factors such as speed, distance to the vehicle ahead, keeping within road markings.</p>
  </div>
  <span class="btn" style="left:79px;top:396px;width:187px;height:56px">READ MORE</span>
  <div class="frame" role="img" aria-label="Rendered view of a driver seated in a car cabin with sensing overlay" style="left:666px;top:58px;width:460px;height:399px;background:linear-gradient(160deg,#d9d9d9 0%,#8f8f8f 50%,#3a3a3a 100%)"></div>
  <div class="dots" style="left:910px;top:470px"><i class="on"></i><i></i><i></i><i></i><i></i></div>
</section>

<section class="expertise">
  <h2 class="heading">STRONG EXPERTISE</h2>
  <p class="quote">" We have many years experience in machine learning, data mining, app development,<br>DevOps and hardware design "</p>
  <h3>We Solve “HARD” Problems For Business</h3>
  <div class="skill" style="left:247px"><svg width="80" height="62" viewBox="0 0 80 62" fill="none" stroke="#0a80c4" stroke-width="2"><rect x="14" y="12" width="46" height="30" rx="2"/><path d="M6 46h62l-4 6H10z"/><circle cx="62" cy="12" r="7"/></svg>Software Development</div>
  <div class="skill" style="left:481px"><svg width="80" height="62" viewBox="0 0 80 62" fill="none" stroke="#0a80c4" stroke-width="2"><circle cx="34" cy="28" r="20"/><ellipse cx="34" cy="28" rx="9" ry="20"/><line x1="14" y1="28" x2="54" y2="28"/><circle cx="56" cy="46" r="7"/><line x1="61" y1="51" x2="70" y2="60"/></svg>IOT System Design</div>
  <div class="skill" style="left:714px"><svg width="80" height="62" viewBox="0 0 80 62" fill="none" stroke="#0a80c4" stroke-width="2"><rect x="20" y="2" width="40" height="58" rx="3"/><line x1="20" y1="12" x2="60" y2="12"/><rect x="27" y="20" width="26" height="12"/><line x1="27" y1="40" x2="53" y2="40"/><line x1="27" y1="47" x2="53" y2="47"/></svg>Machine learning solutions</div>
</section>

<section class="band" style="top:2044px;height:518px">
  <svg class="abs" style="left:0;top:0" width="1200" height="518" viewBox="0 0 1200 518"><polygon points="0,0 70,0 0,130" fill="#0a80c4"/><polygon points="0,455 440,455 520,518 0,518" fill="#0a80c4"/></svg>
  <div class="frame" role="img" aria-label="Photo of mechanics inspecting a red car in a workshop" style="left:79px;top:59px;width:457px;height:396px;background:linear-gradient(180deg,#c9ccd0 0%,#9a9ea4 45%,#a02a2a 70%,#4a4a4a 100%)"></div>
  <div class="dots" style="left:207px;top:481px"><i class="on"></i><i></i><i></i><i></i><i></i></div>
  <h2 class="heading product-title" style="right:81px;top:62px">WHEELWISE</h2>
  <div class="product-copy" style="right:81px;top:122px;width:540px;text-align:right">
    <p>Wheelwise is a machine learning system that tracks and analyzes live used car trading markets. It learns every aspect of a car ads, through which, it creates powerful market intelligence for all parties in the used car ecosystem:</p>
    <p>It gives inexperienced buyers independent market consensus price, depreciation and approximated running costs for cars they are interested.</p>
    <p>It provides dealerships comprehensive market intelligence including demands, supply, consensus price, and expected market life of car</p>
  </div>
  <span class="btn" style="left:937px;top:361px;width:187px;height:54px">READ MORE</span>
</section>

<section class="help">
  <h2 class="heading">HOW CAN WE HELP</h2>
  <div class="help-item" style="left:79px"><svg width="80" height="60" viewBox="0 0 80 60" fill="none" stroke="#0a80c4" stroke-width="2.5"><rect x="4" y="14" width="44" height="30"/><path d="M48 22h14l12 12v10H48z"/><circle cx="18" cy="48" r="6" fill="#fff"/><circle cx="60" cy="48" r="6" fill="#fff"/></svg><span class="rule"></span><p>Acquire more development capacity and get Results fast</p></div>
  <div class="help-item" style="left:462px"><svg width="60" height="64" viewBox="0 0 60 64" fill="none" stroke="#0a80c4" stroke-width="2.5"><path d="M22 6h16l-5 10h-6z"/><path d="M27 16C12 24 6 38 8 50c1 8 8 12 22 12s21-4 22-12c2-12-4-26-19-34z"/><text x="30" y="50" text-anchor="middle" font-family="Open Sans,Arial,sans-serif" font-size="22" font-weight="700" fill="#0a80c4" stroke="none">$</text></svg><span class="rule"></span><p>Avoid the overhead incurred by frequent scaling of your development team</p></div>
  <div class="help-item" style="left:806px"><svg width="64" height="64" viewBox="0 0 64 64" fill="none" stroke="#0a80c4" stroke-width="2.5"><circle cx="32" cy="32" r="26"/><path d="M12 22c8 4 14 2 20 8s2 12 8 16 10-2 14-6"/><path d="M20 52c2-8 8-10 6-18"/></svg><span class="rule"></span><p>Reach a wide spectrum of expertise.</p></div>
</section>

<section class="contact">
  <h2>CONTACT US</h2>
  <p class="sub">Ready to turn your vision into reality? Contact us to get started.</p>
  <div class="field" style="left:77px;top:193px;width:342px;height:38px">Name *</div>
  <div class="field" style="left:77px;top:247px;width:342px;height:38px">Email *</div>
  <div class="field" style="left:77px;top:301px;width:342px;height:38px">Phone *</div>
  <div class="field" style="left:430px;top:193px;width:340px;height:146px">Message *</div>
  <span class="btn">SUBMIT</span>

  <div class="info" style="top:196px"><svg width="22" height="30" viewBox="0 0 22 30"><path d="M11 1a10 10 0 0 0-10 10c0 8 10 18 10 18s10-10 10-18A10 10 0 0 0 11 1z" fill="#fff"/><circle cx="11" cy="11" r="4" fill="#0a7cc0"/></svg>
    <div style="top:-2px;font-family:'Exo 2',Arial,sans-serif;font-weight:700;font-size:16px">KORVEL</div>
    <div style="top:22px">101 - Lorem ipsum is the simple<br>dummy text of print and type</div>
  </div>
  <div class="info" style="top:276px"><svg width="24" height="24" viewBox="0 0 24 24"><path d="M6 2l4 5-2 3c1 3 3 5 6 6l3-2 5 4-3 4C10 22 2 14 2 5z" fill="#fff"/></svg><div style="top:1px;font-size:15px">123 456 7890</div></div>
  <div class="info" style="top:326px"><svg width="26" height="20" viewBox="0 0 26 20"><rect x="1" y="1" width="24" height="18" fill="#fff"/><polyline points="1,1 13,11 25,1" fill="none" stroke="#0a7cc0" stroke-width="2"/></svg><div style="top:0;font-size:15px">info@korvel.com</div></div>
  <span class="social" style="left:811px"></span>
  <span class="social" style="left:861px"></span>
  <span class="social" style="left:910px"></span>
</section>

<footer class="site-footer">© KORVEL - 2018 All Right Reserved.</footer>

</body>
</html>
```